Progressive European Honey Business needs minimalistic packaging design

Hello - thank you for your interest in our brief. We are Honey Plinks, a London based Honey business, importing only the best honey Europe has to offer. Our values are deeply rooted with in progressive liberal values and we are looking for minimalist packaging, which reflects that.

We are looking for a design, which dimensions fit with our packaging option (Vessio Glass Jar | HEIGHT 90mm | DIAMETER 63mm). We will require a various output files (High Resolution JPEG (CMYK Colors 300 dpi) Source File Ai, PSD, PDF, Printing files (die cut, die folding) and a 3D Mockup of the packaging for use within digital commerce platforms.

We must be able to adjust the free text on the label front and it should include the following:
Brand Name
Honey type
Limited edition No. X / 100 ( X being the number of purchase i.e. 25 / 100)
EU Honey, Single Orgin (Germany)
(c) The net weight (250g)

The back must include room for additional information (again adjustable by us) and the following:
“Unsuitable for children under 12 months”
(b) The appropriate durability declaration

In total, we are looking for
a) A front label
b) A back label
c) A seal (round) including the attached bee and logo included in the Zip file.
Do note that a) & b) can also be combined into one design as long as the symmetry on the jar stays intact.

The final design should communicate modern aesthetics, high quality, that are slightly provocative and pop off the shelves.

Hi folks, sorry for the delay in completing this project, but my business partner had a leak in his house. We planned to finalise our review today, but this will have to wait until it's no longer raining in his livingroom. Our sincere apologies!

• See branding guidelines

• Must follow the branding guideline and fonts provided as attachment

```html
<!DOCTYPE html>
<html lang="en">
<head>
<meta charset="utf-8">
<title>Honey Plinks – Front Label</title>
<link href="https://fonts.googleapis.com/css2?family=Outfit:wght@300;400;600;700;800&display=swap" rel="stylesheet">
<style>
  :root {
    --page-bg: #f4f4f4;
    --label-black: #050505;
    --pattern-dark: #141414;
    --pattern-light: #242424;
    --brand-orange: #f0622a;
    --text-white: #ffffff;
    --pill-text: #111111;
  }
  * { margin: 0; padding: 0; box-sizing: border-box; }
  html, body {
    width: 1200px;
    height: 750px;
    overflow: hidden;
    background: var(--page-bg);
    font-family: "Outfit", sans-serif;
  }
  .canvas {
    position: relative;
    width: 1200px;
    height: 750px;
  }
  .front-label {
    position: absolute;
    left: 340px;
    top: 48px;
    width: 520px;
    height: 654px;
    background: var(--label-black);
  }
  .wave-pattern {
    position: absolute;
    left: 20px;
    top: 18px;
    right: 20px;
    bottom: 18px;
    background: linear-gradient(135deg, var(--pattern-light) 0%, var(--pattern-dark) 50%, var(--pattern-light) 100%);
  }
  .label-content {
    position: absolute;
    inset: 0;
    color: var(--text-white);
    text-align: center;
  }
  .brand-name {
    position: absolute;
    left: 0; right: 0;
    top: 152px;
    font-weight: 800;
    font-size: 42px;
    letter-spacing: 1px;
    color: var(--brand-orange);
    text-transform: uppercase;
  }
  .honey-type {
    position: absolute;
    left: 0; right: 0;
    top: 298px;
    font-weight: 700;
    font-size: 66px;
    letter-spacing: -0.5px;
  }
  .origin-row {
    position: absolute;
    left: 0; right: 0;
    top: 442px;
    display: flex;
    justify-content: center;
    align-items: center;
    gap: 16px;
  }
  .origin-mark {
    text-align: left;
    line-height: 1;
  }
  .origin-mark .origin-title {
    display: block;
    font-weight: 700;
    font-size: 24px;
  }
  .origin-mark .origin-sub {
    display: block;
    font-weight: 300;
    font-size: 13px;
    letter-spacing: 2.4px;
    margin-top: 1px;
  }
  .origin-divider {
    width: 2px;
    height: 90px;
    background: var(--text-white);
  }
  .origin-country {
    font-weight: 400;
    font-size: 24px;
    letter-spacing: 0.5px;
  }
  .edition {
    position: absolute;
    left: 0; right: 0;
    top: 559px;
    display: flex;
    justify-content: center;
    align-items: center;
    gap: 6px;
    font-weight: 300;
    font-size: 17px;
    letter-spacing: 4px;
  }
  .edition-number {
    background: var(--text-white);
    color: var(--pill-text);
    font-weight: 600;
    font-size: 14px;
    letter-spacing: 0;
    padding: 8px 10px;
    border-radius: 14px;
  }
  .net-weight {
    position: absolute;
    left: 0; right: 0;
    top: 612px;
    line-height: 1;
  }
  .net-weight .weight-value {
    display: block;
    font-weight: 700;
    font-size: 18px;
  }
  .net-weight .weight-caption {
    display: block;
    font-weight: 300;
    font-size: 13px;
    letter-spacing: 3px;
    margin-top: 6px;
  }
</style>
</head>
<body>
  <main class="canvas">
    <section class="front-label">
      <div class="wave-pattern" role="img" aria-label="Diagonal wavy line pattern in dark grey on black"></div>
      <div class="label-content">
        <h1 class="brand-name">Honey Plinks</h1>
        <h2 class="honey-type">Honey type</h2>
        <div class="origin-row">
          <div class="origin-mark">
            <span class="origin-title">EU HONEY</span>
            <span class="origin-sub">SINGLE ORIGIN</span>
          </div>
          <span class="origin-divider"></span>
          <span class="origin-country">Germany</span>
        </div>
        <p class="edition">Limited edition No.<span class="edition-number">25/100</span></p>
        <p class="net-weight">
          <span class="weight-value">(250g)</span>
          <span class="weight-caption">Net Weight</span>
        </p>
      </div>
    </section>
  </main>
</body>
</html>
```